KBT Business Cards

We require business cards for our business. We would like a matte black back to the card, with our logo centred in the middle. The front side of the card is open to design.

Target Market(s)

Clients looking for legal services (professional)

Industry/Entity Type

Legal

Contact Information for Business Card

Doran Kelbrath
Partner
Mobile: 0461 738 524
Email: doran@kbtlaw.co
Website: www.kbtlaw.co
Level 3, 118 Wendmore Street
Sydney NSW 2000

Font styles to use
Other font styles liked:
• Avenir

Colors
f04a50
ffffff
1b1b1b

Requirements
Must have
• Black back with logo included in the centre of the card.
• Our font is Avenir.

```html
<!DOCTYPE html>
<html lang="en">
<head>
<meta charset="utf-8">
<title>KBT Business Cards</title>
<link rel="stylesheet" href="https://fonts.googleapis.com/css2?family=Roboto:wght@400;500;700&display=swap">
<style>
  :root {
    --brand-red: #f04a50;
    --crimson: #c8203f;
    --white: #ffffff;
    --card-black: #1b1b1b;
    --card-face: #1e1f21;
    --rule: #6b6b6b;
    --backdrop: #e4e4e4;
    --muted: #d9d9d9;
  }
  * { box-sizing: border-box; margin: 0; padding: 0; }
  html, body { width: 1200px; height: 1108px; overflow: hidden; }
  body {
    background: var(--backdrop);
    font-family: "Roboto", Arial, sans-serif;
    position: relative;
  }
  .card {
    position: absolute;
    top: 222px;
    width: 400px;
    height: 664px;
    border-radius: 26px;
    background: var(--card-face);
    overflow: hidden;
    color: var(--white);
  }
  .card--front { left: 170px; }
  .card--back { left: 630px; }

  /* Front */
  .brand {
    position: absolute;
    top: 150px;
    left: 56px;
    display: flex;
    align-items: center;
    gap: 18px;
  }
  .brand__square {
    width: 30px;
    height: 30px;
    background: var(--crimson);
    flex: none;
  }
  .brand__name {
    font-weight: 700;
    font-size: 29px;
    line-height: 30px;
    letter-spacing: -0.3px;
    color: var(--white);
    text-transform: uppercase;
  }
  .person {
    position: absolute;
    top: 362px;
    left: 0;
    width: 100%;
    text-align: center;
  }
  .person__name {
    font-weight: 700;
    font-size: 22px;
    letter-spacing: 0.2px;
    color: var(--crimson);
    text-transform: uppercase;
  }
  .person__role {
    font-size: 17px;
    color: var(--muted);
    margin-top: 2px;
  }
  .contact-rule {
    position: absolute;
    top: 432px;
    left: 40px;
    width: 320px;
    height: 28px;
    display: flex;
    align-items: center;
    justify-content: center;
    gap: 6px;
  }
  .contact-rule::before,
  .contact-rule::after {
    content: "";
    flex: 1;
    height: 1px;
    background: var(--rule);
  }
  .contact-rule svg { width: 26px; height: 26px; display: block; }
  .contact-list {
    position: absolute;
    top: 476px;
    left: 0;
    width: 100%;
    text-align: center;
    list-style: none;
    font-size: 18px;
    line-height: 28px;
    color: var(--muted);
  }
  .address-rule {
    position: absolute;
    top: 568px;
    left: 95px;
    width: 210px;
    height: 1px;
    background: var(--rule);
  }
  .address {
    position: absolute;
    top: 580px;
    left: 0;
    width: 100%;
    text-align: center;
    font-style: normal;
    font-size: 18px;
    line-height: 26px;
    color: var(--muted);
  }

  /* Back */
  .back-texture {
    position: absolute;
    inset: 0;
    background:
      radial-gradient(ellipse at 35% 30%, rgba(255,255,255,0.07) 0%, rgba(255,255,255,0) 60%),
      linear-gradient(160deg, #2c2d30 0%, #242528 45%, #1b1c1e 100%);
  }
  .back-brand {
    position: absolute;
    top: 50%;
    left: 50%;
    transform: translate(-50%, -50%);
    display: flex;
    align-items: center;
    gap: 22px;
  }
  .back-brand__square {
    width: 38px;
    height: 38px;
    background: var(--crimson);
    flex: none;
  }
  .back-brand__name {
    font-weight: 700;
    font-size: 40px;
    line-height: 41px;
    letter-spacing: -0.4px;
    color: var(--white);
    text-transform: uppercase;
  }
</style>
</head>
<body>

<section class="card card--front" aria-label="Card front">
  <div class="brand">
    <span class="brand__square"></span>
    <p class="brand__name">Kelbrath<br>Bryce<br>Tolland</p>
  </div>

  <div class="person">
    <h1 class="person__name">Doran Kelbrath</h1>
    <p class="person__role">Partner</p>
  </div>

  <div class="contact-rule">
    <svg viewBox="0 0 26 26" aria-label="Phone">
      <circle cx="13" cy="13" r="12" fill="var(--crimson)"/>
      <path d="M9 7.5c.8-.5 1.6 0 2 .8l.8 1.7c.3.6.1 1.2-.4 1.6l-.6.5c.6 1.4 1.7 2.5 3.1 3.1l.5-.6c.4-.5 1-.7 1.6-.4l1.7.8c.8.4 1.3 1.2.8 2-.6 1-1.8 1.6-3 1.3-3.4-.9-6-3.5-6.9-6.9-.3-1.2.3-2.4 1.3-3z" fill="#1b1b1b"/>
    </svg>
    <svg viewBox="0 0 26 26" aria-label="Email">
      <circle cx="13" cy="13" r="12" fill="var(--crimson)"/>
      <rect x="7" y="9" width="12" height="8.5" rx="1" fill="none" stroke="#1b1b1b" stroke-width="1.6"/>
      <path d="M7.5 9.5l5.5 4.5 5.5-4.5" fill="none" stroke="#1b1b1b" stroke-width="1.6"/>
    </svg>
    <svg viewBox="0 0 26 26" aria-label="Website">
      <circle cx="13" cy="13" r="12" fill="var(--crimson)"/>
      <circle cx="13" cy="13" r="6" fill="none" stroke="#1b1b1b" stroke-width="1.5"/>
      <ellipse cx="13" cy="13" rx="2.6" ry="6" fill="none" stroke="#1b1b1b" stroke-width="1.3"/>
      <path d="M7 13h12" stroke="#1b1b1b" stroke-width="1.3"/>
    </svg>
  </div>

  <ul class="contact-list">
    <li>0461 738 524</li>
    <li>doran@kbtlaw.co</li>
    <li>www.kbtlaw.co</li>
  </ul>

  <div class="address-rule"></div>
  <address class="address">Level 3, 118 Wendmore<br>Street Sydney NSW 2000</address>
</section>

<section class="card card--back" aria-label="Card back">
  <div class="back-texture" role="img" aria-label="Subtle repeating tonal brand-mark pattern across the matte black card back"></div>
  <div class="back-brand">
    <span class="back-brand__square"></span>
    <p class="back-brand__name">Kelbrath<br>Bryce<br>Tolland</p>
  </div>
</section>

</body>
</html>
```